The logo name is "Harbor Skin". The name of the product will be "Cutaneous Comfort". This product is specifically formulated for amputees. Therefore under the product name it should state "for amputees". The catch phrase will be "Experience Harbor find Calmness"
These are the things we need on the label:
Logo, product name, "for amputees", "Experience Harbor find Calmness", Safe, Effective, Directions: spray on problem areas, no need to dry off. harborskin.example, Made in Canada, 500ml.
The MOST IMPORTANT and therefore the most prominent thing on this lable will be the LOGO! The second most prominent thing will be the word "Comfort" We want to keep it very plain, very simple, very unclutered. Keep in mind that this lable will be placed on a white bottle or have a white back ground. The 500ml white PE bottle with trigger sprayer will have a tear drop label. See attached die line (S-294).
We want to stay with the colours that goes with the colour scheme of the logo. See attached logo. Soft colours. We do not want a picture! We would like the lable to be classy and rich.
Updates
The logo name is "Harbor Skin". The name of the product will be "Cutaneous Comfort". This product is specificlly formulated for amputees. Therefore under the product name it should state "for amputees". The catch phrase will be "Experience Harbor find Calmness"
Logo, product name, "for amputees", catch phrase "Experience Harbor find Calmness", Clean, Safe, Effective, Directions: spray on problem areas, no need to dry off. Also Harbor Skin Corpation, harborskin.example, Made in Canada, 500ml.
We want to stay with the colour scheme of the logo. See attached logo. Soft colours. We do not want a picture! We would like the lable to be classy and rich.
This is the offical directive that came from the governing panal of this lable. This panal it not know where it wanted to take this lable that would represent this line until they review all of your submissions, thank you for all your talented hard work. But now it is clear it is time to regroup and hit this objective.
Project Deadline Extended
Reason: New restrictions on lable wording for this product.
Target Market(s)
Amputees and Parents of.
Industry/Entity Type
Product
Requirements
Must have
- Final product to be in a pdf or an illustrator file

```html
<!DOCTYPE html>
<html lang="en">
<head>
<meta charset="UTF-8">
<title>Harbor Skin – Cutaneous Comfort Label</title>
<link rel="stylesheet" href="https://fonts.googleapis.com/css2?family=Alegreya:wght@700&family=Open+Sans:wght@600;700&family=Encode+Sans+Condensed:wght@600&display=swap">
<style>
  :root {
    --paper: #ffffff;
    --label-cream: #fffdf4;
    --label-gold: #fde49a;
    --label-edge: #c9c9c9;
    --forest: #123d2c;
    --teal: #1f8a6a;
    --teal-soft: #5bb596;
    --orange: #f49b26;
    --ink: #1e2b22;
  }
  html, body {
    margin: 0;
    padding: 0;
    width: 1200px;
    height: 900px;
    overflow: hidden;
    background: var(--paper);
  }
  .canvas {
    position: relative;
    width: 1200px;
    height: 900px;
    font-family: "Open Sans", Arial, sans-serif;
  }
  .die-line {
    position: absolute;
    left: 0;
    top: 0;
  }
  .brand {
    position: absolute;
    left: 450px;
    top: 428px;
    width: 300px;
    display: flex;
    align-items: center;
    gap: 12px;
  }
  .brand-mark {
    width: 30px;
    height: 30px;
    background: var(--teal-soft);
    flex: none;
  }
  .brand-name {
    font-family: "Alegreya", Georgia, serif;
    font-weight: 700;
    font-size: 44px;
    line-height: 1;
    color: var(--forest);
    white-space: nowrap;
  }
  .product-name {
    position: absolute;
    left: 400px;
    top: 538px;
    width: 365px;
    text-align: center;
    white-space: nowrap;
    line-height: 1;
  }
  .product-type {
    font-family: "Alegreya", Georgia, serif;
    font-weight: 700;
    font-size: 21px;
    color: var(--teal);
  }
  .product-hero {
    font-family: "Alegreya", Georgia, serif;
    font-weight: 700;
    font-size: 37px;
    letter-spacing: 0.5px;
    color: var(--forest);
  }
  .audience {
    position: absolute;
    left: 495px;
    top: 582px;
    width: 163px;
    height: 24px;
    border-radius: 5px;
    background: var(--orange);
    color: var(--paper);
    font-weight: 700;
    font-size: 16px;
    line-height: 24px;
    text-align: center;
  }
  .tagline {
    position: absolute;
    left: 480px;
    top: 612px;
    width: 200px;
    margin: 0;
    text-align: center;
    font-weight: 700;
    font-size: 13px;
    line-height: 16px;
    color: var(--teal);
  }
  .fine-print {
    position: absolute;
    left: 455px;
    top: 662px;
    margin: 0;
    font-weight: 600;
    font-size: 7.5px;
    line-height: 9px;
    color: var(--ink);
  }
  .fine-print p { margin: 0 0 6px; }
  .volume {
    position: absolute;
    left: 667px;
    top: 708px;
    font-family: "Encode Sans Condensed", "Arial Narrow", sans-serif;
    font-weight: 600;
    font-size: 20px;
    color: var(--ink);
  }
  .view-caption {
    position: absolute;
    left: 0;
    top: 777px;
    width: 1172px;
    text-align: center;
    font-weight: 700;
    font-size: 15px;
    color: #111;
  }
</style>
</head>
<body>
<div class="canvas">
  <svg class="die-line" width="1200" height="900" viewBox="0 0 1200 900" aria-hidden="true">
    <defs>
      <radialGradient id="label-glow" cx="600" cy="450" r="330" gradientUnits="userSpaceOnUse">
        <stop offset="0" stop-color="var(--label-cream)" stop-opacity="1" style="stop-color:#ffffff"/>
        <stop offset="0.35" style="stop-color:#fff8dc"/>
        <stop offset="1" style="stop-color:#fde397"/>
      </radialGradient>
      <clipPath id="teardrop-clip">
        <path id="teardrop-shape" d="M646,103 C600,125 520,235 470,330 C432,405 403,475 400,560 L400,700 Q402,752 452,752 L718,752 Q765,752 765,700 L765,560 C765,430 722,215 668,110 Q660,100 646,103 Z"/>
      </clipPath>
      <path id="badge-top" d="M622,200 A20,20 0 0 1 662,200"/>
      <path id="badge-bottom" d="M616,200 A26,26 0 0 0 668,200"/>
    </defs>
    <path d="M646,103 C600,125 520,235 470,330 C432,405 403,475 400,560 L400,700 Q402,752 452,752 L718,752 Q765,752 765,700 L765,560 C765,430 722,215 668,110 Q660,100 646,103 Z" fill="url(#label-glow)" stroke="#c9c9c9" stroke-width="1"/>
    <rect class="name-band" x="395" y="530" width="375" height="60" fill="#ffffff" clip-path="url(#teardrop-clip)"/>
    <g class="quality-badge">
      <circle cx="642" cy="200" r="14" fill="none" stroke="#1f8a6a" stroke-width="3"/>
      <circle cx="642" cy="200" r="8" fill="#1f8a6a"/>
      <text font-family="Open Sans, sans-serif" font-weight="700" font-size="11" fill="#1f8a6a">
        <textPath href="#badge-top" startOffset="50%" text-anchor="middle">Safe</textPath>
      </text>
      <text font-family="Open Sans, sans-serif" font-weight="700" font-size="11" fill="#1f8a6a" dy="8">
        <textPath href="#badge-bottom" startOffset="50%" text-anchor="middle">Effective</textPath>
      </text>
    </g>
  </svg>

  <div class="brand">
    <span class="brand-mark"></span>
    <span class="brand-name">Harbor Skin</span>
  </div>

  <div class="product-name">
    <span class="product-type">Cutaneous</span>
    <span class="product-hero">COMFORT</span>
  </div>

  <div class="audience">For Amputees</div>

  <p class="tagline">Experience Harbor<br>Find Calmness</p>

  <div class="fine-print">
    <p>DIRECTIONS:<br>Spray on problem areas,<br>no need to dry off.</p>
    <p>Harbor Skin Corporation<br>www.harborskin.example</p>
    <p>MADE IN CANADA</p>
  </div>

  <div class="volume">500mL</div>

  <div class="view-caption">Front</div>
</div>
</body>
</html>
```